Morlavik APP redesign and color change

I am looking for a new design for my app. Please see the attached current design.

Currently, I have a functioning app but the colors and design are awful!
The logo is great but the rest of the app needs a refresh.
(Logo hi res not yet available but will upload soon.)
New colors or anything that is cutting edge.

Basically: It is a secure social media app within a school system where the teachers, students and parents can text, exchange photos, plan curriculum, etc.

I NEED ONLY landing page with a new look!
Looking for one distinct design for the landing page with new look.
The developer will apply this one design towards the rest of the pages/app screens.

Because part of the social media I need the feel and look of what is now the trend. Something that will attract and keep the client(s) interested. I am really leaving all the creative work to the designer and open to any suggestions.

Target Market(s)

Schools, community, teachers, students, colleges, sport teams

Industry/Entity Type

Non Profit

Font styles to use
Serif
Sans Serif

Colors

Designer to choose colors to be used in the design.

Requirements
Must have
• Sharp, trendy, millennial feel
Nice to have
• Up to designer
Should not have
• Up to designer

```html
<!DOCTYPE html>
<html lang="en">
<head>
<meta charset="UTF-8">
<title>Morlavik — Landing</title>
<link rel="stylesheet" href="https://fonts.googleapis.com/css2?family=Roboto:wght@400;500&display=swap">
<style>
  :root {
    --stage: #ebe7e3;
    --screen: #ffffff;
    --ink: #2b3552;
    --ink-soft: #4a5470;
    --tone-grey: #dcd7d4;
    --tone-red: #dc8c80;
    --tone-red-deep: #d2837a;
    --tone-gold: #c9a650;
    --tone-light: #e4e2de;
    --btn-login: #c07f7c;
    --btn-signup: #b38a3b;
    --badge-ring: #ece9e6;
    --brand: #b38a3b;
  }
  * { box-sizing: border-box; margin: 0; padding: 0; }
  html, body {
    width: 1200px;
    height: 800px;
    overflow: hidden;
    background: var(--stage);
    font-family: "Roboto", sans-serif;
  }
  .canvas {
    width: 1200px;
    height: 800px;
    display: flex;
    align-items: center;
    justify-content: center;
  }
  .app-screen {
    position: relative;
    width: 420px;
    height: 746px;
    background: var(--screen);
    overflow: hidden;
    box-shadow: 0 10px 40px rgba(60, 40, 30, 0.15);
  }
  .hero-collage {
    position: absolute;
    top: 0;
    left: 0;
    width: 420px;
    height: 480px;
    display: block;
  }
  .brand-badge {
    position: absolute;
    left: 210px;
    top: 210px;
    width: 112px;
    height: 112px;
    margin: -56px 0 0 -56px;
    border-radius: 50%;
    background: var(--screen);
    border: 6px solid var(--badge-ring);
    display: flex;
    align-items: center;
    justify-content: center;
  }
  .brand-name {
    font-size: 17px;
    font-weight: 500;
    color: var(--brand);
    letter-spacing: 0.3px;
  }
  .join-panel {
    position: absolute;
    left: 0;
    right: 0;
    top: 520px;
    text-align: center;
  }
  .join-title {
    font-size: 25px;
    font-weight: 500;
    color: var(--ink);
    margin-bottom: 12px;
  }
  .join-tagline {
    font-size: 13px;
    line-height: 1.5;
    color: var(--ink-soft);
    max-width: 260px;
    margin: 0 auto;
  }
  .join-actions {
    display: flex;
    justify-content: center;
    gap: 14px;
    margin-top: 28px;
  }
  .btn {
    width: 138px;
    height: 44px;
    border-radius: 22px;
    border: none;
    color: #ffffff;
    font-family: "Roboto", sans-serif;
    font-size: 15px;
    font-weight: 500;
  }
  .btn-login { background: var(--btn-login); }
  .btn-signup { background: var(--btn-signup); }
</style>
</head>
<body>
<main class="canvas">
  <section class="app-screen">
    <svg class="hero-collage" viewBox="0 0 420 480" aria-hidden="false">
      <defs>
        <clipPath id="collage-edge">
          <polygon points="0,0 420,0 420,430 0,480"/>
        </clipPath>
      </defs>
      <g clip-path="url(#collage-edge)">
        <polygon role="img" aria-label="Photo of a smiling student, grey tint" fill="var(--tone-grey)" points="0,0 158,0 210,210 0,196"/>
        <polygon role="img" aria-label="Photo of a classroom desk, red tint" fill="var(--tone-red)" points="158,0 420,0 420,112 210,210"/>
        <polygon role="img" aria-label="Photo of a student outdoors, gold tint" fill="var(--tone-gold)" points="420,112 420,330 210,210"/>
        <polygon role="img" aria-label="Photo of a cheerful student, light tint" fill="var(--tone-light)" points="210,210 420,330 420,480 250,480"/>
        <polygon role="img" aria-label="Photo of a young man, gold tint" fill="var(--tone-gold)" opacity="0.85" points="0,196 210,210 0,392"/>
        <polygon role="img" aria-label="Photo of a teacher with a phone, red tint" fill="var(--tone-red-deep)" points="0,392 210,210 250,480 0,480"/>
      </g>
    </svg>

    <div class="brand-badge">
      <span class="brand-name">Morlavik</span>
    </div>

    <div class="join-panel">
      <h1 class="join-title">Join Today</h1>
      <p class="join-tagline">Interact with your Teachers students and Parents in better way</p>
      <div class="join-actions">
        <button class="btn btn-login" type="button">Login</button>
        <button class="btn btn-signup" type="button">Sign up</button>
      </div>
    </div>
  </section>
</main>
</body>
</html>
```